Landing Page and Logo for Auto-Blogging Platform

I created a platform that allows users to start a blog for their business, hobby, charity, etc. I need a landing page where users can learn about the platform, benefits of consistent blogging, SEO value, plans/pricing, etc. The landing page needs to have multiple call to action buttons encouraging the visitor to register/sign up for a free trial.

In addition to the landing page, I need a page for users to establish the settings for their blog. This page should be a fairly simple form, intended for the user to enter a few details to set up their blog:
1. Name of Blog
2. Up to 10 topics and/or keywords the blog should focus on
3. Theme: Color-scheme and logo upload for blog.

I have attached the specifications of the platform's functionality so you can better understand how it works, plans/pricing, etc.

I also need a logo for the business. The name of the platform is PostNook.

Target Market(s)

Website owners, bloggers, business owners

Industry/Entity Type

Technology, Internet, web design

Coding

Coded - Design and coding required

Number of Pages Required

2 page

Colors
0054AA
0677BA
7BADD7
CADEEF
E8F1F8
0094D4
00A9DD
6FCCEA
C7EBF8
E9F6FB

Requirements
Must have
• Eye-catching design but fairly light on content (keep it simple and brief.)
Nice to have
• Eye-catching yet simple design, clean and easy to understand what we are offering.
Should not have
• Too much “wordy” and confusing content.

```html
<!DOCTYPE html>
<html lang="en">
<head>
<meta charset="utf-8">
<title>PostNook – Automate Your Blog Posting with AI</title>
<link href="https://fonts.googleapis.com/css2?family=Arimo:wght@400;700&family=Lato:wght@400;700&display=swap" rel="stylesheet">
<style>
:root{
  --navy:#0054AA; --blue:#0677BA; --sky:#0094D4; --cyan:#00A9DD;
  --soft:#7BADD7; --pale:#CADEEF; --mist:#E8F1F8; --ice:#E9F6FB;
  --ink:#1d1d1f; --text:#555; --dark:#2a2a2c; --white:#fff;
}
*{box-sizing:border-box;margin:0;padding:0}
html,body{width:1200px;height:4109px;overflow:hidden;background:#fff}
body{position:relative;font-family:"Lato",sans-serif;color:var(--ink)}
section,header,footer{position:absolute;left:0;width:1200px}
.abs{position:absolute}
.h-font{font-family:"Arimo",sans-serif}
.btn{position:absolute;display:flex;align-items:center;justify-content:center;border-radius:24px;font-family:"Arimo",sans-serif;font-weight:700;font-size:15px;color:#fff}
.btn-cyan{background:var(--cyan)}
.btn-navy{background:var(--navy)}
.btn-white{background:#fff;color:var(--cyan)}
.sec-title{position:absolute;left:0;width:100%;text-align:center;font-family:"Arimo",sans-serif;font-size:31px;color:var(--sky)}
.sec-title b{color:var(--navy)}

/* header */
.site-header{top:0;height:107px;background:#fff}
.top-line{position:absolute;left:0;top:0;width:519px;height:5px;background:var(--navy)}
.brand{position:absolute;display:flex;align-items:center;gap:12px;font-family:"Arimo",sans-serif;font-size:32px;color:#222}
.brand-dot{width:48px;height:48px;border-radius:50%;background:var(--sky)}
.nav a{position:absolute;top:48px;font-size:16px;color:#333;text-decoration:none}
.nav a.active{color:var(--sky)}

/* hero */
.hero{top:107px;height:620px}
.hero-visual{position:absolute;inset:0;background:linear-gradient(100deg,#1b2a3a 0%,#2d4a52 40%,#3a5a5e 60%,#12314c 100%)}
.hero h1{position:absolute;left:110px;top:66px;font-family:"Arimo",sans-serif;font-weight:400;font-size:63px;line-height:78px;color:#fff}
.hero h1 b{font-weight:700}
.hero p{position:absolute;left:110px;top:232px;width:545px;font-size:16.5px;line-height:26px;color:#fff}
.dots{position:absolute;left:576px;top:520px;display:flex;gap:8px}
.dots i{width:11px;height:11px;border-radius:50%;border:2px solid #fff}
.dots i.on{background:#fff}

/* about */
.about{top:727px;height:598px}
.screen-art{position:absolute;left:80px;top:60px;width:542px;height:450px;border-radius:14px;background:linear-gradient(180deg,#e9edf2,#cfd6de)}
.about h2{position:absolute;left:693px;top:96px;font-family:"Arimo",sans-serif;font-weight:400;font-size:31px;color:var(--sky)}
.about h2 b{color:var(--navy)}
.about p{position:absolute;left:693px;top:153px;width:400px;font-size:15.5px;line-height:25.7px;color:var(--text)}

/* plans */
.plans{top:1325px;height:609px;background:var(--mist)}
.plan{position:absolute;top:148px;width:300px;height:383px;background:#fff;box-shadow:0 4px 14px rgba(0,40,90,.08)}
.plan.featured{background:var(--navy);color:#fff}
.plan .label{position:absolute;left:33px;top:28px;font-family:"Arimo",sans-serif;font-size:13px}
.plan .rule{position:absolute;left:0;right:0;top:69px;height:1px;background:#e6e6e6}
.plan.featured .rule{background:rgba(255,255,255,.25)}
.plan .price{position:absolute;left:33px;top:90px;font-family:"Arimo",sans-serif;font-weight:700;font-size:43px}
.plan .price sup{font-weight:400;font-size:13px;color:var(--sky);vertical-align:top;position:relative;top:6px;margin-left:6px}
.plan .lead{position:absolute;left:35px;top:156px;font-size:15px}
.plan ul{position:absolute;left:35px;top:196px;list-style:none}
.plan li{display:flex;align-items:center;gap:12px;height:34.5px;font-size:13px}
.plan .btn{left:35px;top:315px;width:152px;height:44px;font-size:14px}

/* benefits */
.benefits{top:1934px;height:532px}
.benefit{position:absolute;top:143px;width:240px;text-align:center}
.benefit .ring{margin:0 auto;width:172px;height:172px;border-radius:50%;background:#fff;box-shadow:0 0 14px rgba(0,0,0,.1);display:flex;align-items:center;justify-content:center}
.benefit .ring.on{background:linear-gradient(135deg,var(--sky),var(--navy))}
.benefit h3{margin-top:22px;font-family:"Arimo",sans-serif;font-size:21px;color:#222}
.benefit .bar{width:34px;height:3px;background:var(--sky);margin:8px auto 14px}
.benefit p{font-size:14.5px;line-height:21px;color:#777}
.arrow{position:absolute;top:2147px;width:32px;height:32px;border-radius:50%}

/* topics */
.topics{top:2466px;height:471px;background:linear-gradient(90deg,var(--navy),var(--sky) 70%,var(--cyan))}
.topics h2{position:absolute;left:112px;top:78px;font-family:"Arimo",sans-serif;font-weight:400;font-size:31px;color:#fff}
.topics ul{position:absolute;left:112px;top:144px;width:470px;list-style:none;color:#fff;font-size:17.5px;line-height:25px}
.topics li{display:flex;gap:14px;margin-bottom:18px}
.topics li svg{flex:none;margin-top:4px}
.photo-frame{position:absolute;left:669px;top:38px;width:420px;height:355px;border:2px solid rgba(255,255,255,.8);border-radius:24px}
.photo{position:absolute;left:686px;top:48px;width:401px;height:327px;border-radius:22px;background:linear-gradient(135deg,#d8e2ea,#5c87b6 55%,#0b3f80)}

/* setup */
.setup{top:2937px;height:798px}
.step{position:absolute;left:198px;width:804px;height:59px;border:2px solid var(--pale);display:flex;align-items:center}
.step .num{width:76px;padding-left:36px;font-family:"Arimo",sans-serif;font-weight:700;font-size:20px;color:#bbb}
.step .name{flex:1;text-align:center;font-family:"Arimo",sans-serif;font-weight:700;font-size:16px;color:#222}
.step .ico{width:59px;height:100%;background:var(--mist);display:flex;align-items:center;justify-content:center}
.step.open{border-color:var(--sky);background:var(--sky);top:151px}
.step.open .num{color:rgba(255,255,255,.6)}
.step.open .name{color:#fff}
.step.open .ico{background:var(--navy)}
.step-body{position:absolute;left:198px;top:210px;width:804px;height:303px;border:2px solid var(--sky);border-top:0}
.step-body h4{position:absolute;left:38px;top:45px;width:320px;font-family:"Arimo",sans-serif;font-size:17.5px;line-height:30px;color:#222}
.step-body p{position:absolute;left:38px;top:117px;width:355px;font-size:13px;line-height:23px;color:#555}
.step-body .art{position:absolute;left:434px;top:32px;width:327px;height:240px;background:linear-gradient(135deg,#27435a,#4f7f96 50%,#152a3d)}

/* footer */
.site-footer{top:3735px;height:374px;background:var(--dark);color:#fff}
.footer-cut{position:absolute;left:0;top:-1px;width:1200px;height:34px}
.col{position:absolute;top:90px;font-size:13.5px;line-height:25.5px}
.col h5{font-family:"Arimo",sans-serif;font-size:15px;margin-bottom:14px}
.contact-row{display:flex;gap:16px;align-items:flex-start;margin-bottom:12px}
.follow{position:absolute;left:112px;top:224px;display:flex;align-items:center;gap:14px;font-size:17px}
.follow i{width:33px;height:33px;border-radius:50%;border:2px solid #fff}
.foot-rule{position:absolute;left:112px;right:112px;top:303px;height:1px;background:#444}
.pay{position:absolute;left:112px;top:319px;display:flex;gap:8px}
.pay i{width:29px;height:27px;background:#fff;border-radius:3px}
.copy{position:absolute;left:454px;top:322px;font-size:13px}
</style>
</head>
<body>

<header class="site-header">
  <div class="top-line"></div>
  <div class="brand" style="left:112px;top:32px"><span class="brand-dot"></span>PostNook</div>
  <nav class="nav">
    <a class="active" href="#" style="left:466px">Home</a>
    <a href="#" style="left:547px">About us</a>
    <a href="#" style="left:646px">Services</a>
    <a href="#" style="left:742px">Plan</a>
    <a href="#" style="left:809px">Contact us</a>
  </nav>
  <svg class="abs" style="left:920px;top:48px" width="18" height="18" viewBox="0 0 18 18"><circle cx="7.5" cy="7.5" r="5.5" fill="none" stroke="#0094D4" stroke-width="2.4"/><path d="M11.5 11.5L16 16" stroke="#0094D4" stroke-width="2.6" stroke-linecap="round"/></svg>
  <div class="btn btn-navy" style="left:974px;top:35px;width:110px;height:43px;font-size:15px">Register</div>
</header>

<section class="hero">
  <div class="hero-visual" role="img" aria-label="Person holding a tablet surrounded by glowing news pages, charts and a world map"></div>
  <svg class="abs" style="left:0;top:490px" width="1200" height="140" viewBox="0 0 1200 140">
    <path d="M0 116 Q420 150 822 236 L822 140 L0 140Z" fill="#fff"/>
    <path d="M0 116 Q420 170 822 236 Q1010 180 1200 145 L1200 140 L1200 0 L1200 145 Q1000 150 822 210 Q420 140 0 110Z" fill="#0094D4"/>
    <path d="M0 113 Q430 165 822 236 Q1010 190 1200 145 L1200 140 L0 140Z" fill="#fff"/>
  </svg>
  <h1>Automate Your<br><b>Blog Posting</b> with AI</h1>
  <p>Transform your blogging experience with our AI-powered platform that not only generates and optimizes content tailored to your audience but also continuously learns and adapts to deliver smarter insights, ensuring your voice stands out in a crowded digital landscape.</p>
  <div class="btn btn-cyan" style="left:110px;top:367px;width:200px;height:39px">Sign up for a free trial</div>
  <div class="dots"><i></i><i class="on"></i><i></i></div>
</section>

<section class="about">
  <div class="screen-art" role="img" aria-label="Desktop monitor showing the blog dashboard with category cards"></div>
  <h2>About <b>The Platform</b></h2>
  <p>The platform will require a list of blog topics. Based on the topics list, the software will need to automatically send prompts to TextGen AI in the specified intervals (monthly, weekly, or daily), receive the blog content, and post it to the blog. Furthermore, the software will need some method of adding at least one image to each blog post. Ideally, this would be achieved by using the StockLens API to retrieve image(s) based on keywords in the blog topic.</p>
  <div class="btn btn-navy" style="left:693px;top:409px;width:202px;height:42px">Sign up for a free trial</div>
</section>

<section class="plans">
  <h2 class="sec-title" style="top:71px;font-weight:400">Our <b>Plans</b></h2>
  <div class="plan" style="left:113px">
    <div class="label">BASE PLAN</div><div class="rule"></div>
    <div class="price">$9.99<sup>/Month</sup></div>
    <div class="lead">1 blog post (up to 2,000 words)</div>
    <ul>
      <li><svg width="16" height="13"><path d="M2 7l4 4 8-9" fill="none" stroke="#0094D4" stroke-width="2.4"/></svg>Lorem ipsum dolor sit amet</li>
      <li><svg width="16" height="13"><path d="M2 7l4 4 8-9" fill="none" stroke="#0094D4" stroke-width="2.4"/></svg>Lorem ipsum dolor sit amet</li>
      <li><svg width="16" height="13"><path d="M2 7l4 4 8-9" fill="none" stroke="#0094D4" stroke-width="2.4"/></svg>Lorem ipsum dolor sit amet</li>
    </ul>
    <div class="btn btn-navy">CHOOSE PLAN</div>
  </div>
  <div class="plan featured" style="left:452px">
    <div class="label">PREMIUM PLAN</div><div class="rule"></div>
    <div class="price">$14.99<sup>week</sup></div>
    <div class="lead">1 blog post (up to 2,000 words)</div>
    <ul>
      <li><svg width="16" height="13"><path d="M2 7l4 4 8-9" fill="none" stroke="#00A9DD" stroke-width="2.4"/></svg>Lorem ipsum dolor sit amet</li>
      <li><svg width="16" height="13"><path d="M2 7l4 4 8-9" fill="none" stroke="#00A9DD" stroke-width="2.4"/></svg>Lorem ipsum dolor sit amet</li>
      <li><svg width="16" height="13"><path d="M2 7l4 4 8-9" fill="none" stroke="#00A9DD" stroke-width="2.4"/></svg>Lorem ipsum dolor sit amet</li>
    </ul>
    <div class="btn btn-cyan">CHOOSE PLAN</div>
  </div>
  <div class="plan" style="left:788px">
    <div class="label">ULTIMATE PLAN</div><div class="rule"></div>
    <div class="price">$24.99<sup>Per day</sup></div>
    <div class="lead">1 blog post (up to 3,000 words)</div>
    <ul>
      <li><svg width="16" height="13"><path d="M2 7l4 4 8-9" fill="none" stroke="#0094D4" stroke-width="2.4"/></svg>Lorem ipsum dolor sit amet</li>
      <li><svg width="16" height="13"><path d="M2 7l4 4 8-9" fill="none" stroke="#0094D4" stroke-width="2.4"/></svg>Lorem ipsum dolor sit amet</li>
      <li><svg width="16" height="13"><path d="M2 7l4 4 8-9" fill="none" stroke="#0094D4" stroke-width="2.4"/></svg>Lorem ipsum dolor sit amet</li>
    </ul>
    <div class="btn btn-navy">CHOOSE PLAN</div>
  </div>
</section>

<section class="benefits">
  <h2 class="sec-title" style="top:62px;font-weight:400">Benefits of <b>Consistent Blogging</b></h2>
  <div class="benefit" style="left:99px">
    <div class="ring"><svg width="70" height="70" viewBox="0 0 70 70" fill="none" stroke="#0054AA" stroke-width="2.5"><rect x="8" y="8" width="48" height="56" rx="3"/><path d="M16 20h32M16 30h20M16 40h32M16 50h24"/><path d="M52 30l12-12 4 4-12 12z" stroke="#0094D4"/></svg></div>
    <h3>Lorem ipsum do</h3><div class="bar"></div>
    <p>Sed ut perspiciatis und omnis iste natus error sit voluptatem accusantium</p>
  </div>
  <div class="benefit" style="left:356px">
    <div class="ring on"><svg width="80" height="80" viewBox="0 0 80 80" fill="none" stroke="#fff" stroke-width="2.5"><path d="M40 8l14 5v10c0 9-6 15-14 18-8-3-14-9-14-18V13z"/><path d="M34 24l5 5 8-9"/><path d="M6 46l14-6 20 12 20-12 14 6M22 56l10 8M32 52l12 10M42 50l10 8"/></svg></div>
    <h3>Lorem ipsum do</h3><div class="bar"></div>
    <p>Sed ut perspiciatis und omnis iste natus error sit voluptatem accusantium</p>
  </div>
  <div class="benefit" style="left:613px">
    <div class="ring"><svg width="70" height="70" viewBox="0 0 70 70" fill="none" stroke="#0054AA" stroke-width="2.5"><rect x="6" y="8" width="58" height="54" rx="3"/><path d="M6 20h58"/><rect x="14" y="28" width="12" height="10" stroke="#0094D4"/><rect x="30" y="28" width="12" height="10"/><rect x="46" y="28" width="12" height="10"/><path d="M14 46h44M14 54h30"/></svg></div>
    <h3>Lorem ipsum do</h3><div class="bar"></div>
    <p>Sed ut perspiciatis und omnis iste natus error sit voluptatem accusantium</p>
  </div>
  <div class="benefit" style="left:870px">
    <div class="ring"><svg width="70" height="70" viewBox="0 0 70 70" fill="none" stroke="#0054AA" stroke-width="2.5"><rect x="8" y="6" width="56" height="58" rx="3"/><path d="M8 16h56"/><path d="M14 24h10v30l-5 6-5-6z" stroke="#0094D4"/><path d="M32 26h24M32 36h24M32 46h24M32 56h16"/></svg></div>
    <h3>Lorem ipsum do</h3><div class="bar"></div>
    <p>Sed ut perspiciatis und omnis iste natus error sit voluptatem accusantium</p>
  </div>
</section>
<svg class="arrow" style="left:59px" viewBox="0 0 32 32"><circle cx="16" cy="16" r="14.5" fill="#fff" stroke="#0094D4" stroke-width="2"/><path d="M18 10l-6 6 6 6" fill="none" stroke="#0094D4" stroke-width="2.4"/></svg>
<svg class="arrow" style="left:1109px" viewBox="0 0 32 32"><circle cx="16" cy="16" r="16" fill="#0054AA"/><path d="M14 10l6 6-6 6" fill="none" stroke="#fff" stroke-width="2.4"/></svg>

<section class="topics">
  <h2>The Blog Topics <b>Of Methods</b></h2>
  <ul>
    <li><svg width="18" height="18"><circle cx="9" cy="9" r="9" fill="#fff"/><path d="M5 9l3 3 5-6" fill="none" stroke="#0054AA" stroke-width="2"/></svg>The user enters them into a table manually.</li>
    <li><svg width="18" height="18"><circle cx="9" cy="9" r="9" fill="#fff"/><path d="M5 9l3 3 5-6" fill="none" stroke="#0054AA" stroke-width="2"/></svg>The user uploads a list of blog topics in CSV format.</li>
    <li><svg width="18" height="18"><circle cx="9" cy="9" r="9" fill="#fff"/><path d="M5 9l3 3 5-6" fill="none" stroke="#0054AA" stroke-width="2"/></svg>AI can create the list of blog topics based on a prompt such as: "Provide a list of 52 blog topics for a handyman business's blog.</li>
  </ul>
  <div class="btn btn-white" style="left:112px;top:346px;width:148px;height:42px">Learn More</div>
  <div class="photo-frame"></div>
  <div class="photo" role="img" aria-label="Hands typing on a laptop showing a news update page"></div>
</section>

<section class="setup">
  <h2 class="sec-title" style="top:80px;font-weight:400">How to Set Up the <b>Auto-Blog</b></h2>
  <div class="step open">
    <div class="num">01</div><div class="name">SELECT FREQUENCY OF AUTOMATED BLOG POSTS</div>
    <div class="ico"><svg width="28" height="26" fill="none" stroke="#fff" stroke-width="2"><rect x="2" y="3" width="22" height="18" rx="2"/><path d="M6 9h14M6 14h9M14 20l10-10"/></svg></div>
  </div>
  <div class="step-body">
    <h4>SELECT FREQUENCY OF AUTOMATED BLOG POSTS</h4>
    <p>Sed ut perspiciatis unde omnis iste natus error sit voluptatem accusantium doloremque laudantium, totam rem aperiam, eaque ipsa quae ab illo inventore veritatis et quasi architecto beatae vitae dicta sunt explicabo.</p>
    <div class="btn btn-navy" style="left:38px;top:223px;width:126px;height:41px">Learn More</div>
    <div class="art" role="img" aria-label="Futuristic computer workstation with glowing screens"></div>
  </div>
  <div class="step" style="top:528px">
    <div class="num">02</div><div class="name">NAME YOUR BLOG STEP</div>
    <div class="ico"><svg width="28" height="26" fill="none" stroke="#7BADD7" stroke-width="2"><rect x="2" y="5" width="20" height="18" rx="2"/><path d="M6 11h12M6 16h8M16 18l10-12"/></svg></div>
  </div>
  <div class="step" style="top:600px">
    <div class="num">03</div><div class="name">SELECT YOUR BLOG TOPICS</div>
    <div class="ico"><svg width="28" height="26" fill="none" stroke="#7BADD7" stroke-width="2"><rect x="3" y="2" width="22" height="22" rx="2"/><path d="M7 8h14M7 13h14M7 18h10"/></svg></div>
  </div>
  <div class="step" style="top:671px">
    <div class="num">04</div><div class="name">GO DO SOMETHING ELSE AND LET AI DO ALL YOUR BLOGGING FOR YOU!</div>
    <div class="ico"><svg width="28" height="26" fill="none" stroke="#7BADD7" stroke-width="2"><rect x="2" y="3" width="24" height="18" rx="2"/><path d="M6 9h8M6 14h8M17 9h5v7h-5z"/></svg></div>
  </div>
</section>

<footer class="site-footer">
  <svg class="footer-cut" viewBox="0 0 1200 34"><path d="M0 0H1200L0 30Z" fill="#fff"/></svg>
  <div class="brand" style="left:112px;top:140px;color:#fff"><span class="brand-dot"></span>PostNook</div>
  <div class="follow">FOLLOW US:<i></i><i></i><i></i></div>
  <div class="col" style="left:480px">
    <h5>CONTACT INFO</h5>
    <div class="contact-row"><svg width="14" height="18"><path d="M7 1a6 6 0 0 1 6 6c0 5-6 10-6 10S1 12 1 7a6 6 0 0 1 6-6z" fill="#0094D4"/><circle cx="7" cy="7" r="2" fill="#2a2a2c"/></svg><span>PostNook<br>Address Comes Here</span></div>
    <div class="contact-row"><svg width="14" height="16"><path d="M3 1l3 3-2 3c1 2 3 4 5 5l3-2 3 3-2 3C7 16 0 9 1 3z" fill="#0094D4"/></svg><span>+1-555-014-2290</span></div>
    <div class="contact-row"><svg width="14" height="16"><rect x="0" y="3" width="14" height="10" fill="#0094D4"/><path d="M0 3l7 5 7-5" fill="none" stroke="#2a2a2c" stroke-width="1.2"/></svg><span>info@postnook.example</span></div>
  </div>
  <div class="col" style="left:758px">
    <h5>QUICK LINKS</h5>
    Home<br>About us<br>Services<br>Plan<br>Contact us
  </div>
  <div class="col" style="left:969px">
    <h5>OTHER LINKS</h5>
    Terms &amp; Conditions<br>Privacy Policy<br>About Us<br>Support
  </div>
  <div class="foot-rule"></div>
  <div class="pay"><i></i><i></i><i></i><i></i><i></i></div>
  <div class="copy">©Copyrights 2024 PostNook. All Rights Reserved.</div>
</footer>

</body>
</html>
```